Letter design, envelope design, and more

Hello, we the Tavrin Gmbh are looking for our shop. Letter C5. Design does not have to be like a business card, so it can have straight lines. Only the color is important. The logo is the text under TaVRin omit.It should not be playful but Profesionel

Font styles to use
Sans Serif

Colors
0555a3
3176b5
85abd2
85cae6
34a7d8
0792cd
cee9f5
cfdfed
000000

Requirements
Must have
• Color like business card, Please, with the text under TaVRin, Correct address Lindmattstr. 4 Zip code 9517 Seldach, as well as Couvert Without addressing only design and logo with TaVrn
Nice to have
• more writing articles
Should not have
• Not too colored, Text under TaVRin, bright colors

```html
<!DOCTYPE html>
<html lang="en">
<head>
<meta charset="utf-8">
<title>Tavrin Gmbh – Letterhead and Envelope</title>
<link href="https://fonts.googleapis.com/css2?family=Arimo:wght@700&family=Source+Sans+3:wght@400;600&display=swap" rel="stylesheet">
<style>
  :root {
    --stage: #e8e8e8;
    --paper: #ffffff;
    --brand: #0555a3;
    --rule: #0792cd;
    --accent: #34a7d8;
    --flap: #85abd2;
    --ink: #4a4a4a;
    --dark: #000000;
    --muted: #3a3a3a;
  }
  * { box-sizing: border-box; margin: 0; padding: 0; }
  html, body { width: 1200px; height: 880px; overflow: hidden; }
  body {
    background: var(--stage);
    position: relative;
    font-family: "Source Sans 3", sans-serif;
  }

  .sheet {
    position: absolute;
    background: var(--paper);
    box-shadow: 0 1px 3px rgba(0,0,0,.18);
  }

  /* Letterhead */
  .letter { left: 80px; top: 106px; width: 472px; height: 668px; }

  .brand {
    position: absolute;
    display: flex;
    align-items: center;
    gap: 6px;
    font-family: "Source Sans 3", sans-serif;
    font-weight: 600;
    color: var(--brand);
    letter-spacing: .5px;
    white-space: nowrap;
  }
  .brand-mark { background: var(--brand); display: block; }
  .letter .brand { left: 38px; top: 30px; font-size: 18px; }
  .letter .brand-mark { width: 24px; height: 24px; }

  .header-rule {
    position: absolute; left: 0; right: 0; top: 70px;
    display: flex; align-items: center;
  }
  .header-rule .line { height: 2px; background: var(--rule); }
  .header-rule .line.long { width: 356px; }
  .header-rule .line.short { flex: 1; }
  .web {
    font-size: 7.5px; letter-spacing: 1.6px; color: var(--muted);
    padding: 0 7px;
  }
  .web .name { color: var(--accent); }

  .salutation {
    position: absolute; left: 41px; top: 151px;
    font-family: "Arimo", sans-serif; font-weight: 700;
    font-size: 10.5px; color: var(--dark);
  }
  .body-copy {
    position: absolute; left: 41px; top: 177px; width: 394px;
    font-size: 10.3px; line-height: 12.3px; color: var(--ink);
    text-align: justify;
  }
  .body-copy p + p { margin-top: 12.3px; }

  .signature {
    position: absolute; left: 40px; top: 470px; width: 90px; height: 40px;
  }

  .contact {
    position: absolute; left: 0; right: 0; top: 645px;
    display: flex; justify-content: center; gap: 18px;
    font-size: 7.4px; color: var(--muted);
  }
  .contact span { display: flex; align-items: center; gap: 3px; }
  .contact svg { display: block; }

  /* Envelope */
  .envelope { left: 606px; top: 348px; width: 514px; height: 426px; }
  .flap { position: absolute; left: 0; top: 0; }
  .envelope .brand { left: 40px; top: 100px; font-size: 19px; }
  .envelope .brand-mark { width: 26px; height: 26px; }
  .footer-rule {
    position: absolute; left: 0; right: 0; top: 388px;
    display: flex; align-items: center;
  }
  .footer-rule .line { flex: 1; height: 2px; background: var(--rule); }
</style>
</head>
<body>

<section class="sheet letter" aria-label="Letterhead">
  <div class="brand"><span class="brand-mark"></span>TAVRIN GMBH</div>

  <div class="header-rule">
    <span class="line long"></span>
    <span class="web">www.<span class="name">tavrin</span>.ch</span>
    <span class="line short"></span>
  </div>

  <p class="salutation">Dear Mr. Aldor,</p>

  <div class="body-copy">
    <p>Lorem Ipsum is simply dummy text of the printing and typesetting industry. Lorem Ipsum has been the industry's standard dummy text ever since the 1500s, when an unknown printer took a galley of type and scrambled it to make a type specimen book. It has survived not only five centuries, but also the leap into electronic typesetting, remaining essentially unchanged.</p>
    <p>The standard chunk of Lorem Ipsum used since the 1500s is reproduced below for those interested. Sections 1.10.32 and 1.10.33 from "de Finibus Bonorum et Malorum" by Cicero are also reproduced in their exact original form, accompanied by English versions from the 1914 translation by H. Rackham</p>
    <p>Lorem Ipsum is simply dummy text of the printing and typesetting industry. Lorem Ipsum has been the industry's standard dummy text ever since the 1500s, when an unknown printer took a galley of type and scrambled it to make a type specimen book. It has survived not only five centuries, but also the leap into electronic typesetting, remaining essentially unchanged. It was popularised in the</p>
    <p>The standard chunk of Lorem Ipsum used since the 1500s is reproduced below for those interested. Sections 1.10.32 and 1.10.33 from "de Finibus Bonorum et Malorum" by Cicero are also reproduced in their exact original form, accompanied by English versions from the 1914 translation by H. Rackham</p>
  </div>

  <div class="signature" role="img" aria-label="Handwritten signature" style="background: linear-gradient(90deg, #f1f1f1, #e6e6e6);"></div>

  <div class="contact">
    <span>
      <svg width="7" height="9" viewBox="0 0 7 9"><path d="M3.5 0A3.5 3.5 0 0 0 0 3.5C0 6 3.5 9 3.5 9S7 6 7 3.5A3.5 3.5 0 0 0 3.5 0z" fill="var(--brand)"/><circle cx="3.5" cy="3.4" r="1.2" fill="#fff"/></svg>
      Lindmattstr. 4&nbsp; 9517 Seldach,
    </span>
    <span>
      <svg width="8" height="8" viewBox="0 0 8 8"><circle cx="4" cy="4" r="3.4" fill="none" stroke="var(--brand)" stroke-width="1"/><path d="M2.4 3.2h3.2M2.4 4.8h3.2" stroke="var(--brand)" stroke-width=".9"/></svg>
      +41 71 555 02 48
    </span>
    <span>
      <svg width="8" height="6" viewBox="0 0 8 6"><rect x=".5" y=".5" width="7" height="5" fill="none" stroke="var(--brand)" stroke-width="1"/><path d="M.5.5L4 3.3 7.5.5" fill="none" stroke="var(--brand)" stroke-width=".9"/></svg>
      info@tavrin.ch
    </span>
  </div>
</section>

<section class="sheet envelope" aria-label="C5 envelope">
  <svg class="flap" width="514" height="63" viewBox="0 0 514 63" aria-hidden="true">
    <path d="M0 63 L6 14 Q8 0 22 0 L492 0 Q506 0 508 14 L514 63 Z" fill="var(--flap)"/>
  </svg>

  <div class="brand"><span class="brand-mark"></span>TAVRIN GMBH</div>

  <div class="footer-rule">
    <span class="line"></span>
    <span class="web">www.<span class="name">tavrin</span>.ch</span>
    <span class="line"></span>
  </div>
</section>

</body>
</html>
```